New Company Letterhead

Hi All

We are looking for a fresh new letterhead. At present we have rolling colour behind our logo but would like one flat colour. See attached for examples of our current letterhead, logos and company colour chart. All information currently contained within the letterhead (i.e. address, ABN, tel, fax, email etc) needs to still be included in the new letterhead. Preferred font is Helvetica or something similar.

Any queries please shout.

Many thanks & best of luck,

Rosalind Pembury
Barwick Estate Agents

Hi Designers Great work so far! Would it be possible to add to your designs the phrase; Done. Different. Preferably in a light grey? Many thanks, Ros

```html
<!DOCTYPE html>
<html lang="en">
<head>
<meta charset="utf-8">
<title>Barwick Estate Agents – Letterhead</title>
<link rel="stylesheet" href="https://fonts.googleapis.com/css2?family=Arimo:wght@400;700&display=swap">
<style>
  :root {
    --brand-teal: #02506e;
    --paper: #ffffff;
    --backdrop: #e4e5e7;
    --footer-grey: #8a8c8f;
    --footer-strong: #6f7174;
  }
  * { box-sizing: border-box; margin: 0; padding: 0; }
  html, body {
    width: 1200px;
    height: 1200px;
    overflow: hidden;
    background: var(--backdrop);
    font-family: "Arimo", "Helvetica Neue", Helvetica, Arial, sans-serif;
  }
  .letterhead {
    position: absolute;
    left: 175px;
    top: 50px;
    width: 850px;
    height: 1100px;
    background: var(--paper);
  }
  .header-band {
    position: absolute;
    left: 0;
    top: 51px;
    width: 100%;
    height: 140px;
    background: var(--brand-teal);
  }
  .company-name {
    position: absolute;
    left: 68px;
    top: 42px;
    color: var(--paper);
    font-weight: 400;
    font-size: 38px;
    letter-spacing: 3px;
    text-transform: uppercase;
    line-height: 1;
  }
  .margin-rule {
    position: absolute;
    left: 67px;
    width: 3px;
    background: var(--brand-teal);
  }
  .margin-rule--top { top: 0; height: 44px; }
  .margin-rule--main { top: 203px; bottom: 0; }
  .company-details {
    position: absolute;
    left: 92px;
    top: 944px;
    color: var(--footer-grey);
    font-size: 11px;
    line-height: 14px;
  }
  .company-details .legal-name {
    font-weight: 700;
    color: var(--footer-strong);
  }
  .company-details .address { margin-bottom: 10px; }
  .contact-list { list-style: none; }
  .contact-list .label {
    display: inline-block;
    width: 16px;
    font-weight: 700;
    color: var(--footer-strong);
  }
</style>
</head>
<body>
  <main class="letterhead">
    <div class="margin-rule margin-rule--top"></div>
    <header class="header-band">
      <div class="company-name">Barwick Estate Agents</div>
    </header>
    <div class="margin-rule margin-rule--main"></div>

    <footer class="company-details">
      <div class="legal-name">Barwick Estate Agents</div>
      <div>ABN: 47 118 305 926</div>
      <div class="address">58 Harbour Street, Kelsworth NSW 2290</div>
      <ul class="contact-list">
        <li><span class="label">P</span>(02) 5550 1842</li>
        <li><span class="label">F</span>(02) 5550 1843</li>
        <li><span class="label">E</span>office@barwickestateagents.com.au</li>
        <li><span class="label">W</span>www.barwickestateagents.com.au</li>
      </ul>
    </footer>
  </main>
</body>
</html>
```